High-end construction company needs a business card design

We need a modern looking business card that draws people in, is memorable and looks so good people will want to sick it on their fridges.
On the first side what is needed are:
Logo
My name - Tomasz Brelwik
Title - Managing Director
Website - www.varkelt.co.uk
Email - tomasz@varkelt.co.uk
Telephone - 020 5194 6281
Mobile - 07845139072
On the back side was is needed is a list of all the services we provide:
-Kitchen Renovations
-Bathroom Renovations
-House Renovations
-Garage Conversions
-Extensions
-Loft Conversions
-Conservatories
-Carpentry
-Tiling
-Electrical
-Plumbing & Heating
-Bricklaying
-Landscaping
-Decorating
-Plastering
We would like the colours to be the same shades as on the logo with grey or black for the words.
Target Market(s)
Anyone who needs building work done
Contact Information for Business Card
This business card is for a construction company which strives to deliver excellent service and quality.
The look and feel of the card should represent this.
Requirements
Must have
- On the first side what is needed are:
Logo
My name - Tomasz Brelwik
Title - Managing Director
Website - www.varkelt.co.uk
Email - tomasz@varkelt.co.uk
Telephone - 020 5194 6281
Mobile - 07845139072
Nice to have
- Cool looking features

```html
<!DOCTYPE html>
<html lang="en">
<head>
<meta charset="utf-8">
<title>Varkelt Construction Ltd – Business Card</title>
<link rel="stylesheet" href="https://fonts.googleapis.com/css2?family=Lato:ital,wght@0,400;0,700;0,900;1,400&display=swap">
<style>
  :root{
    --bg:#e7e8e4;
    --green-deep:#4a8c3f;
    --green-lime:#5cb531;
    --green-text:#4f9a37;
    --ink:#3a3a3a;
    --ink-soft:#555;
    --paper:#ffffff;
  }
  *{box-sizing:border-box;margin:0;padding:0}
  html,body{width:1200px;height:847px;overflow:hidden}
  body{background:var(--bg);font-family:"Lato",sans-serif;position:relative}
  .card{position:absolute;width:540px;height:309px;border-radius:3px;box-shadow:0 10px 28px rgba(0,0,0,.18)}
  .card--back{left:70px;top:100px;background:var(--green-deep);border-bottom:6px solid var(--green-lime)}
  .card--front{left:590px;top:430px;background:var(--paper);border-bottom:6px solid var(--green-lime);display:flex;align-items:center}
  .brand{display:flex;align-items:center;gap:10px;font-weight:900;text-transform:uppercase;letter-spacing:1px}
  .brand__mark{width:16px;height:16px;flex:none}
  .card--back .brand{position:absolute;top:58px;left:0;right:0;justify-content:center;color:var(--paper);font-size:22px}
  .card--back .brand__mark{background:var(--green-lime)}
  .services{position:absolute;left:40px;right:40px;top:130px;color:var(--paper);font-style:italic;font-size:15px;line-height:25px;text-align:left}
  .card--front .brand{width:250px;justify-content:center;color:var(--green-text);font-size:19px;flex-direction:column;gap:8px;text-align:center;line-height:1.15}
  .card--front .brand__mark{background:var(--green-lime);width:18px;height:18px}
  .divider{width:1px;height:150px;background:var(--green-lime);margin:0 26px 0 4px}
  .person__name{color:var(--green-text);font-weight:900;font-size:27px}
  .person__title{color:var(--ink-soft);font-size:15px;margin:2px 0 16px}
  .contacts{list-style:none;color:var(--ink);font-size:15px;line-height:22px}
  .contacts li{display:flex;align-items:center;gap:10px}
  .contacts svg{width:14px;height:14px;flex:none;fill:var(--green-lime)}
  .contacts .accent{color:var(--green-text)}
</style>
</head>
<body>
  <section class="card card--back" aria-label="Card back: services">
    <div class="brand"><span class="brand__mark"></span>Varkelt Construction Ltd</div>
    <p class="services">
      Kitchen Renovations | Bathroom Renovations | House Renovations<br>
      Garage Conversions | Extensions | Loft Conversions | Conservatories<br>
      Carpentry | Tiling | Electrical | Plumbing &amp; Heating<br>
      Bricklaying | Landscaping | Decorating | Plastering
    </p>
  </section>

  <section class="card card--front" aria-label="Card front: contact details">
    <div class="brand"><span class="brand__mark"></span>Varkelt<br>Construction Ltd</div>
    <div class="divider"></div>
    <div class="person">
      <h1 class="person__name">Tomasz Brelwik</h1>
      <p class="person__title">Managing Director</p>
      <ul class="contacts">
        <li><svg viewBox="0 0 16 16"><path d="M3 1h3l1.5 4-2 1.5a9 9 0 0 0 4 4L11 8.5l4 1.5v3a2 2 0 0 1-2 2A12 12 0 0 1 1 3a2 2 0 0 1 2-2z"/></svg>020 5194 6281</li>
        <li><svg viewBox="0 0 16 16"><path d="M4 0h8a1 1 0 0 1 1 1v14a1 1 0 0 1-1 1H4a1 1 0 0 1-1-1V1a1 1 0 0 1 1-1zm1 2v10h6V2zm3 11a1 1 0 1 0 0 2 1 1 0 0 0 0-2z"/></svg>07845139072</li>
        <li><svg viewBox="0 0 16 16"><path d="M0 3h16v10H0zm1.5 1.2v.3L8 9l6.5-4.5v-.3z"/></svg>tomasz@varkelt.co.uk</li>
        <li><svg viewBox="0 0 16 16"><path d="M8 0a8 8 0 1 0 0 16A8 8 0 0 0 8 0zm0 1.5c1 0 2 1.8 2.3 4.5H5.7C6 3.3 7 1.5 8 1.5zM5.6 7.5h4.8a14 14 0 0 1 0 1H5.6a14 14 0 0 1 0-1zM8 14.5c-1 0-2-1.8-2.3-4.5h4.6C10 12.7 9 14.5 8 14.5z"/></svg><span>www.<span class="accent">varkelt</span>.co.uk</span></li>
      </ul>
    </div>
  </section>
</body>
</html>
```